Awesome photographers card for an awesome new business

Double sided business card Black background and silver logo in middle on one side. Details on otherside. please keep it simple

Industry/Entity Type

Photographer

Contact Information for Business Card

Gerald Fenwick
0452817360
GeraldFenwickPhotography47@mailbox.test
www.GeraldFenwickPhotography.test.au
Instagram _Gerald_fenwick

Requirements
Must have
• My logo in Silver
• please use instagram logo instead of "Instagram"

```html
<!DOCTYPE html>
<html lang="en">
<head>
<meta charset="utf-8">
<title>Gerald Fenwick Photography – Business Card</title>
<link rel="stylesheet" href="https://fonts.googleapis.com/css2?family=Montserrat:wght@600&family=Questrial&display=swap">
<style>
  :root {
    --page-bg: #d9d4ce;
    --card-top: #eceae7;
    --card-bottom: #d6d3cf;
    --card-edge: rgba(255,255,255,0.7);
    --ink: #3a3a3c;
    --ink-soft: #55565a;
    --rule: #4a4a4c;
    --band-dark: #38383b;
    --band-light: #9a9a9d;
    --band-text: #d8d8da;
    --aperture-a: rgba(255,255,255,0.55);
    --aperture-b: rgba(200,198,195,0.25);
  }
  html, body {
    margin: 0;
    width: 1200px;
    height: 969px;
    overflow: hidden;
    background: var(--page-bg);
  }
  .canvas {
    position: relative;
    width: 1200px;
    height: 969px;
  }
  .card {
    position: absolute;
    left: 100px;
    top: 199px;
    width: 1000px;
    height: 571px;
    border-radius: 22px;
    overflow: hidden;
    background: linear-gradient(160deg, var(--card-top), var(--card-bottom));
    box-shadow: inset 0 0 0 2px var(--card-edge), 0 10px 30px rgba(0,0,0,0.12);
    font-family: "Questrial", "Century Gothic", sans-serif;
    color: var(--ink);
  }
  .aperture-art {
    position: absolute;
    left: -16px;
    top: 35px;
    width: 480px;
    height: 480px;
    border-radius: 50%;
    background: radial-gradient(circle at 40% 40%, var(--aperture-a), var(--aperture-b));
  }
  .brand-mark {
    position: absolute;
    left: 660px;
    top: 150px;
    display: flex;
    align-items: center;
    gap: 12px;
  }
  .brand-dot {
    width: 16px;
    height: 16px;
    border-radius: 50%;
    background: var(--ink);
  }
  .brand-name {
    font-size: 28px;
    color: var(--ink);
    letter-spacing: 1px;
  }
  .holder-name {
    position: absolute;
    left: 52px;
    top: 334px;
    margin: 0;
    font-family: "Montserrat", "Century Gothic", sans-serif;
    font-weight: 600;
    font-size: 29px;
    letter-spacing: 1px;
    text-transform: uppercase;
    color: var(--ink);
  }
  .name-rule {
    position: absolute;
    left: 52px;
    top: 381px;
    width: 880px;
    height: 2px;
    background: var(--rule);
  }
  .contact-list {
    position: absolute;
    left: 56px;
    top: 396px;
    margin: 0;
    padding: 0;
    list-style: none;
    font-size: 22px;
    color: var(--ink-soft);
  }
  .contact-list li {
    display: flex;
    align-items: center;
    height: 31px;
  }
  .contact-icon {
    width: 20px;
    height: 20px;
    margin-right: 18px;
    fill: var(--ink);
  }
  .social-square {
    width: 17px;
    height: 17px;
    margin: 0 19px 0 2px;
    border-radius: 3px;
    background: var(--ink);
  }
  .footer-band {
    position: absolute;
    left: 0;
    bottom: 0;
    width: 1000px;
    height: 50px;
  }
  .website {
    position: absolute;
    left: 507px;
    bottom: 12px;
    font-size: 24px;
    color: var(--band-text);
    letter-spacing: 0.5px;
  }
</style>
</head>
<body>
<div class="canvas">
  <section class="card">
    <div class="aperture-art" role="img" aria-label="Faint camera aperture decoration"></div>

    <div class="brand-mark">
      <span class="brand-dot"></span>
      <span class="brand-name">Gerald Fenwick</span>
    </div>

    <h1 class="holder-name">Gerald Fenwick</h1>
    <div class="name-rule"></div>

    <ul class="contact-list">
      <li>
        <svg class="contact-icon" viewBox="0 0 24 24" aria-hidden="true"><path d="M6.6 10.8a15.1 15.1 0 0 0 6.6 6.6l2.2-2.2c.3-.3.7-.4 1-.2 1.1.4 2.3.6 3.6.6.6 0 1 .4 1 1V20c0 .6-.4 1-1 1A17 17 0 0 1 3 4c0-.6.4-1 1-1h3.5c.6 0 1 .4 1 1 0 1.3.2 2.5.6 3.6.1.3 0 .7-.2 1z"/></svg>
        <span>0452817360</span>
      </li>
      <li>
        <svg class="contact-icon" viewBox="0 0 24 24" aria-hidden="true"><path d="M2 5h20v14H2z M2 5l10 7 10-7" fill="var(--ink)"/><path d="M2.5 5.5l9.5 6.5 9.5-6.5" fill="none" stroke="#e6e4e1" stroke-width="1.6"/></svg>
        <span>GeraldFenwickPhotography47@mailbox.test</span>
      </li>
      <li>
        <span class="social-square"></span>
        <span>Gerald_fenwick</span>
      </li>
    </ul>

    <svg class="footer-band" viewBox="0 0 1000 50" aria-hidden="true">
      <rect x="0" y="20" width="520" height="18" fill="var(--band-light)" opacity="0.6"/>
      <polygon points="480,0 1000,0 1000,50 440,50" fill="var(--band-dark)"/>
    </svg>
    <span class="website">www.GeraldFenwickPhotography.test.au</span>
  </section>
</div>
</body>
</html>
```